Brightwave Reach - Business Card

We need a business card for a Social Media Marketing company that specializes in online marketing for small businesses in Canada using common Social Media platforms such as Pixlora, Chatterly, Blinkpost & Quibber.

I have uploaded a copy of our logo which I would like utilized in the business card. We would like the business card to be modern yet classy design.

Our website is www.brightwavereach.ca

Industry/Entity Type

Marketing

Contact Information for Business Card

Email: info@brightwavereach.ca
Website: www.brightwavereach.ca
Telephone: 604-555-0193

Colors

Designer to choose colors to be used in the design.

Requirements
Must have
• Social Media icons on reverse
• Please add some designs with color.

```html
<!DOCTYPE html>
<html lang="en">
<head>
<meta charset="utf-8">
<title>Brightwave Reach – Business Card</title>
<link href="https://fonts.googleapis.com/css2?family=Open+Sans:wght@400;700&display=swap" rel="stylesheet">
<style>
  :root {
    --page-bg: #2b2624;
    --card-bg: #141414;
    --card-edge: #1f1f1f;
    --ink: #f2f2f2;
    --ink-soft: #bdbdbd;
    --ink-faint: #4a4a4a;
    --rule: #8a8a8a;
    --accent: #e0322f;
    --accent-2: #f29a1f;
  }
  * { margin: 0; padding: 0; box-sizing: border-box; }
  html, body {
    width: 1200px; height: 864px; overflow: hidden;
    background: var(--page-bg);
    font-family: "Open Sans", Arial, sans-serif;
  }
  .sheet {
    width: 1200px; height: 864px;
    display: flex; flex-direction: column;
    align-items: center; justify-content: center; gap: 28px;
  }
  .card {
    position: relative;
    width: 680px; height: 388px;
    background: var(--card-bg);
    border: 1px solid var(--card-edge);
    box-shadow: 0 14px 30px rgba(0,0,0,.45);
    overflow: hidden;
  }
  .accent-band {
    position: absolute; left: 0; right: 0; bottom: 0; height: 6px;
    background: linear-gradient(90deg, var(--accent), var(--accent-2));
  }

  /* Back side */
  .card--back .brand-mark {
    position: absolute; left: 0; right: 0; top: 110px;
    text-align: center;
    font-weight: 700; font-size: 40px; letter-spacing: 1px;
    text-transform: uppercase; color: var(--ink-faint);
  }
  .social-row {
    position: absolute; left: 40px; right: 40px; top: 230px;
    display: flex; align-items: center; gap: 14px;
  }
  .social-row .rule { flex: 1; height: 1px; background: var(--rule); }
  .social-item {
    display: flex; align-items: center; gap: 6px;
    font-size: 13px; color: var(--ink-soft);
  }
  .social-item .dot {
    width: 12px; height: 12px; border-radius: 50%;
    background: var(--accent);
  }

  /* Front side */
  .card--front .brand-mark {
    position: absolute; left: 44px; top: 160px; width: 270px;
    display: flex; align-items: center; gap: 12px;
    font-weight: 700; font-size: 30px; text-transform: uppercase;
    color: var(--ink); line-height: 1.1;
  }
  .brand-mark .square { width: 16px; height: 16px; background: var(--accent); flex: none; }
  .divider {
    position: absolute; left: 340px; top: 110px;
    width: 2px; height: 170px;
    background: linear-gradient(180deg, var(--accent), var(--accent-2));
  }
  .details {
    position: absolute; left: 372px; top: 128px; color: var(--ink);
  }
  .details .name { font-weight: 700; font-size: 20px; letter-spacing: .5px; }
  .details .role { font-size: 17px; color: var(--accent-2); margin-bottom: 22px; }
  .contact { list-style: none; font-size: 17px; }
  .contact li { display: flex; align-items: center; gap: 10px; line-height: 28px; }
  .contact svg { width: 15px; height: 15px; flex: none; }
  .contact .solid { fill: var(--accent); }
  .contact .line { fill: none; stroke: var(--accent); }
</style>
</head>
<body>
<main class="sheet">

  <section class="card card--back" aria-label="Card back">
    <div class="brand-mark">Brightwave Reach</div>
    <div class="social-row">
      <span class="rule"></span>
      <span class="social-item"><span class="dot"></span>Chatterly</span>
      <span class="social-item"><span class="dot"></span>Pixlora</span>
      <span class="social-item"><span class="dot"></span>Blinkpost</span>
      <span class="social-item"><span class="dot"></span>Quibber</span>
      <span class="rule"></span>
    </div>
    <span class="accent-band"></span>
  </section>

  <section class="card card--front" aria-label="Card front">
    <div class="brand-mark"><span class="square"></span>Brightwave Reach</div>
    <span class="divider"></span>
    <div class="details">
      <p class="name">DANIEL MOORE</p>
      <p class="role">CEO/FOUNDER</p>
      <ul class="contact">
        <li>
          <svg viewBox="0 0 16 16" aria-hidden="true"><path class="solid" d="M3 1h3l1.5 4-2 1.2a9 9 0 0 0 4.3 4.3L11 8.5l4 1.5v3a2 2 0 0 1-2 2A12 12 0 0 1 1 3a2 2 0 0 1 2-2z"/></svg>
          604-555-0193
        </li>
        <li>
          <svg viewBox="0 0 16 16" aria-hidden="true"><path class="line" stroke-width="1.6" d="M1 3h14v10H1z M2 4l6 5 6-5"/></svg>
          info@brightwavereach.ca
        </li>
        <li>
          <svg viewBox="0 0 16 16" aria-hidden="true"><circle class="line" cx="8" cy="8" r="6.5" stroke-width="1.5"/><path class="line" stroke-width="1.2" d="M1.5 8h13M8 1.5c-3 3.5-3 9.5 0 13M8 1.5c3 3.5 3 9.5 0 13"/></svg>
          www.brightwavereach.ca
        </li>
      </ul>
    </div>
    <span class="accent-band"></span>
  </section>

</main>
</body>
</html>
```